Namecard Designs+Logo for a High End Automobile Company

We need a new business card for our company called Nordel Motorwerk.

www.nordelmotorwerk.example.sg
Our new website will be up in 2.5 months time.

We sell used and brand new continental cars like Valcrest, KTR, Almira, Dunvale and etc. Currently we are operating from 2 offices in Singapore and United Kingdom.

We want a design which is serious. We are open to colours but try to keep it at a maximum of 3 colours.

We prefer something simple and minimal. We are open to 2 sides printing or even 2 sided namecards. Both UK and Singapore company offices address must be in; either side by side, front and back, or even 2 sided cards.

The logo can be a text logo, emblem, abstract, pictorial or combination.

We are printing with Printlyx.com so please kindly follow the printing guideline.

http://uk.printlyx.example/help/faq/templates-and-guidelines.html

Rich and Car Enthusiasts

Printing

• Our 2 offices; UK and Singapore.

Our slogan which is " The Automobile Specialist"
• Not more than 3 colours

```html
<!DOCTYPE html>
<html lang="en">
<head>
<meta charset="utf-8">
<title>Nordel Motorwerk – Business Card</title>
<link rel="stylesheet" href="https://fonts.googleapis.com/css2?family=PT+Serif:wght@400;700&display=swap">
<style>
  :root {
    --orange: #f79a3a;
    --ink: #1f1f1f;
    --paper: #ffffff;
    --guide: #9a9a9a;
    --silver-light: #e4e4e4;
    --silver-mid: #bdbdbd;
    --silver-dark: #8a8a8a;
  }
  html, body {
    margin: 0;
    padding: 0;
    width: 800px;
    height: 1200px;
    overflow: hidden;
    background: var(--paper);
    font-family: "PT Serif", Georgia, serif;
  }
  p, h2, address { margin: 0; }
  .sheet {
    position: relative;
    width: 800px;
    height: 1200px;
  }
  .trim-guide {
    position: absolute;
    border: 0 dotted var(--guide);
  }
  .trim-guide--front { left: 0; top: 571px; width: 800px; border-top-width: 1px; }
  .trim-guide--back-top { left: 6px; top: 617px; width: 794px; border-top-width: 1px; }
  .trim-guide--back-side { left: 6px; top: 617px; height: 583px; border-left-width: 1px; }

  .card {
    position: absolute;
    box-sizing: border-box;
    border: 2px solid var(--orange);
    border-radius: 0 26px 0 26px;
    overflow: hidden;
    background: var(--paper);
  }

  /* Front */
  .card--front { left: 34px; top: 34px; width: 726px; height: 477px; }
  .front__band {
    position: absolute;
    left: 0; top: 0; right: 0;
    height: 224px;
    background: var(--orange);
  }
  .slogan {
    color: var(--paper);
    letter-spacing: 0.22em;
    white-space: nowrap;
    line-height: 1;
  }
  .front__slogan {
    position: absolute;
    right: 16px;
    top: 166px;
    font-size: 20px;
  }
  .car-visual {
    position: absolute;
    background: linear-gradient(180deg, var(--silver-light) 0%, var(--silver-mid) 55%, var(--silver-dark) 100%);
  }
  .front__car {
    left: 0; top: 252px;
    width: 275px; height: 194px;
    border-radius: 0 90px 40px 0;
  }
  .wordmark {
    font-weight: 700;
    color: var(--ink);
    text-transform: uppercase;
    white-space: nowrap;
    line-height: 1;
  }
  .front__wordmark {
    position: absolute;
    left: 294px;
    top: 362px;
    font-size: 33px;
  }

  /* Back */
  .card--back { left: 42px; top: 680px; width: 726px; height: 477px; }
  .back__band {
    position: absolute;
    left: 0; right: 0; top: 89px; bottom: 0;
    background: var(--orange);
  }
  .back__wordmark {
    position: absolute;
    left: 11px;
    top: 62px;
    font-size: 22px;
  }
  .back__slogan {
    position: absolute;
    left: 13px;
    top: 5px;
    font-size: 12px;
  }
  .office {
    position: absolute;
    top: 138px;
    color: var(--ink);
  }
  .office__title {
    margin-bottom: 14px;
    font-weight: 400;
    font-size: 19px;
    line-height: 1.05;
    color: var(--paper);
  }
  .office__title small {
    font-size: 13px;
    letter-spacing: 0.03em;
  }
  .office__address {
    font-style: normal;
    font-weight: 700;
    font-size: 13.5px;
    line-height: 1.22;
  }
  .office--uk { right: 225px; text-align: right; }
  .office--sg { left: 540px; text-align: left; }
  .office--sg .office__title { margin-bottom: 8px; }
  .back__car {
    left: 0; right: 0; bottom: 0;
    height: 212px;
    border-radius: 160px 60px 0 0;
  }
</style>
</head>
<body>
<main class="sheet">
  <section class="card card--front" aria-label="Card front">
    <div class="front__band">
      <p class="slogan front__slogan">The Automobile Specialist</p>
    </div>
    <div class="car-visual front__car" role="img" aria-label="Front view of a silver convertible car"></div>
    <div class="wordmark front__wordmark">Nordel Motorwerk</div>
  </section>

  <div class="trim-guide trim-guide--front"></div>
  <div class="trim-guide trim-guide--back-top"></div>
  <div class="trim-guide trim-guide--back-side"></div>

  <section class="card card--back" aria-label="Card back">
    <div class="wordmark back__wordmark">Nordel Motorwerk</div>
    <div class="back__band">
      <p class="slogan back__slogan">The Automobile Specialist</p>
    </div>
    <div class="car-visual back__car" role="img" aria-label="Side view of a silver convertible car with the roof down"></div>
    <div class="office office--uk">
      <h2 class="office__title">UK <small>OFFICE</small></h2>
      <address class="office__address">18 Harlow Street.<br>City, London.</address>
    </div>
    <div class="office office--sg">
      <h2 class="office__title">SINGAPORE<br><small>OFFICE</small></h2>
      <address class="office__address">7 Kestrel Grove<br>Rd Block 3B<br>Singapore 410227</address>
    </div>
  </section>
</main>
</body>
</html>
```